KLORA product web page

We need a new web design for our KLORA product page. You can find more information about the project on the current web site - www.klora.example

What we need from a new design (uncoded):
- landing pages + template
- all information on one page
- the design should be focused on the product - light bulb + app
- web site should be with some dynamics like a background with parallax effect in the current version
- fonts should be chosen
- a number of illustrations should be designed

Here is schema for a new design: https://files.examplehost.net/d/draw-7QpX2mLk9RtYv4Hs/edit

Here is a document with all texts for a new design: https://files.examplehost.net/d/doc-3WnZ8bJf5KcUe1Ga/edit

Illustrations to use:
v1 - https://files.examplehost.net/f/fold-A1kT9pQw2ZxR
v2 - https://files.examplehost.net/f/fold-B7mH4sLv6YcN

iOS screens: https://files.examplehost.net/f/fold-C3rJ8dKe1WuP

KLORA logo: https://files.examplehost.net/f/fold-D5nF2gTb9XoM
Updates

I forgot to add the definition text "KLORA - is.." to the document with texts. Sorry, my mistake.

Target Market(s)

25-45 year old adults who are interested in "smart" devices for their health.

Industry/Entity Type

Brintel

Colors

Designer to choose colors to be used in the design.

Requirements
Must have
• - landing pages + template
- fonts should be chosen

```html
<!DOCTYPE html>
<html lang="en">
<head>
<meta charset="utf-8">
<title>KLORA — Color</title>
<link href="https://fonts.googleapis.com/css2?family=Lato:wght@400;700&display=swap" rel="stylesheet">
<style>
  :root {
    --band-light: #c8c0df;
    --header-bg: #ffffff;
    --brand: #7466ae;
    --brand-nav: #7a68b4;
    --nav-ink: #111111;
    --stage-bg: #8b82bd;
    --heading-ink: #3b335c;
    --body-ink: #3f3760;
    --dot-idle: #c8c0df;
    --dot-active: #ffffff;
    --footer-bg: #7c73a8;
    --footer-ink: #cfc9e6;
  }
  * { margin: 0; padding: 0; box-sizing: border-box; }
  html, body { width: 1200px; height: 1000px; overflow: hidden; }
  body {
    font-family: "Lato", Arial, sans-serif;
    background: var(--stage-bg);
    position: relative;
  }
  .top-band {
    position: absolute; left: 0; top: 0; width: 1200px; height: 120px;
    background: var(--band-light);
  }
  .site-header {
    position: absolute; left: 0; top: 30px; width: 1200px; height: 60px;
    background: var(--header-bg);
  }
  .brand-badge {
    position: absolute; left: 141px; top: -10px; width: 80px; height: 80px;
    border-radius: 50%; background: var(--brand);
    display: flex; align-items: center; justify-content: center;
    color: #ffffff; font-weight: 700; font-size: 14px; letter-spacing: 1px;
    text-decoration: none;
  }
  .main-nav {
    position: absolute; right: 140px; top: 0; height: 60px;
    display: flex; align-items: center; gap: 53px;
  }
  .main-nav a {
    font-size: 22px; letter-spacing: 4.2px; color: var(--nav-ink);
    text-decoration: none; font-weight: 400;
  }
  .main-nav a.is-current { color: var(--brand-nav); font-weight: 700; }

  .section-dots {
    position: absolute; left: 20px; top: 459px; list-style: none;
    display: flex; flex-direction: column; gap: 15px;
  }
  .section-dots li {
    width: 15px; height: 15px; border-radius: 50%; background: var(--dot-idle);
  }
  .section-dots li.is-active { background: var(--dot-active); }

  .feature-art {
    position: absolute; left: 148px; top: 326px; width: 344px; height: 386px;
    border-radius: 28px;
    background: radial-gradient(ellipse at 50% 50%, #57b9d9 0%, #8fc4d6 28%, #d9d6e6 60%, #9a92c6 100%);
    opacity: .85;
  }

  .feature-copy {
    position: absolute; left: 590px; top: 382px; width: 460px;
  }
  .feature-title {
    font-size: 24px; font-weight: 700; letter-spacing: 3px;
    color: var(--heading-ink); margin-bottom: 30px;
  }
  .feature-text {
    font-size: 16px; line-height: 25px; color: var(--body-ink);
  }
  .feature-tagline {
    margin-top: 25px; font-size: 16px; line-height: 25px; font-weight: 700;
    color: var(--heading-ink);
  }

  .site-footer {
    position: absolute; left: 0; top: 961px; width: 1200px; height: 39px;
    background: var(--footer-bg);
  }
  .footer-link {
    position: absolute; left: 141px; top: 11px;
    font-size: 14px; font-weight: 700; color: var(--footer-ink); text-decoration: none;
  }
  .copyright {
    position: absolute; right: 148px; top: 10px;
    display: flex; align-items: center; gap: 8px;
    font-size: 11px; color: var(--footer-ink);
  }
  .copyright .brand-name { font-size: 16px; font-weight: 700; letter-spacing: 1px; }
</style>
</head>
<body>
  <div class="top-band"></div>
  <header class="site-header">
    <a class="brand-badge" href="#">KLORA</a>
    <nav class="main-nav">
      <a class="is-current" href="#">PRE-ORDER</a>
      <a href="#">BLOG</a>
      <a href="#">CONTACTS</a>
      <a href="#">RU</a>
    </nav>
  </header>

  <ul class="section-dots">
    <li></li><li></li><li class="is-active"></li><li></li><li></li><li></li>
  </ul>

  <div class="feature-art" role="img" aria-label="Illustration of a smartphone with a row of coloured circles across its screen, the central blue one ticked"></div>

  <section class="feature-copy">
    <h2 class="feature-title">KLORA &amp; COLOR</h2>
    <p class="feature-text">Experiment with millions of colors! Pick any color from the screen of your mobile device and enjoy the ambience.<br>LED lightbulb KLORA can transform conventional lighting into the night lights of Seattle or bring in the rich summer hues of Provence.<br>Enliven your fantasies or raise your best memories in one click. Change the atmosphere around you by changing colors.</p>
    <p class="feature-tagline">You will literally see the world in a new light.</p>
  </section>

  <footer class="site-footer">
    <a class="footer-link" href="#">CONTACTS</a>
    <div class="copyright"><span>COPYRIGHT ©</span><span class="brand-name">KLORA</span></div>
  </footer>
</body>
</html>
```